Ledger Lanternfox Powerpoint with Marshal Valorline Type Theme

Need powerpoint template with matching colors and different slide options. Logo and colors to be used can be found at ledgerlanternfox.example. Want brightly colored slide deck that is readable form the back of a room, but highlights colors. I will be incorporating Quizzap into the slides to gamify my presentations.

Target Market(s)

Tech

Industry/Entity Type

IT, specifically database, but crossing over to mental health in IT, important note this is not for a company, this is just for a professional building a brand

Font styles to use
Sans Serif

Colors
0054AA
0677BA
7BADD7
CADEEF
E8F1F8
EB3D1F
EC4F4E
F09395
F8D3D4
FCEDEE

Requirements
Must have
• My Logo in the bottom corner, front page, a thank your page, question page, content page, content page with two columns, content page with graphs, and icons to be used in the primary colors of the logos, About Me Page, Break Slides, Demo break slide
Should not have
• Lighter shades of colors, I want to pop out where colors are used, I want spacing and font size to be readable from the back of a room, most likely black text and white background

```html
<!DOCTYPE html>
<html lang="en">
<head>
<meta charset="utf-8">
<title>Ledger Lanternfox – Presentation Theme</title>
<link href="https://fonts.googleapis.com/css2?family=Poppins:wght@300;400;500;600;700&display=swap" rel="stylesheet">
<style>
:root{
  --navy:#1c3f7f;
  --navy-dark:#16346b;
  --navy-deep:#12295a;
  --red:#e8262c;
  --red-soft:#f09395;
  --gray:#7b7b7b;
  --ink:#2a2a2a;
  --muted:#6b6b6b;
  --paper:#ffffff;
  --canvas:#e4e4e6;
  --line:#dfe3ea;
}
*{box-sizing:border-box;margin:0;padding:0}
html,body{width:1200px;height:2952px;overflow:hidden;background:var(--canvas);font-family:"Poppins",sans-serif;color:var(--ink)}
.deck{display:grid;grid-template-columns:repeat(3,387px);grid-auto-rows:217px;gap:9px;padding:11px}
.slide{position:relative;overflow:hidden;background:var(--paper)}
.slide.navy{background:var(--navy)}
.abs{position:absolute}
.photo{position:absolute}
.photo-navy{background:linear-gradient(135deg,#2b4f8f 0%,#1c3f7f 55%,#15336c 100%)}
.photo-gray{background:linear-gradient(135deg,#b9c2cf,#6f7f95)}
.brand{font-weight:700;color:var(--red);display:inline-flex;align-items:center;gap:4px;white-space:nowrap;line-height:1}
.brand .dot{width:1em;height:1em;border-radius:50%;background:var(--red);display:inline-block}
.brand.light{color:#fff}.brand.light .dot{background:#fff}
.side{position:absolute;left:5px;top:72px;writing-mode:vertical-rl;transform:rotate(180deg);font-size:6px;font-weight:700;color:var(--red);letter-spacing:.2px}
.corner{position:absolute;left:5px;top:5px;width:9px;height:9px;border-radius:50%;background:var(--red);border:2px solid var(--navy)}
.pg{position:absolute;left:6px;bottom:4px;font-size:5px;color:var(--muted)}
.hd{position:absolute;font-weight:600;font-size:16px;color:var(--navy);line-height:1.2}
.hd::after{content:"";display:block;width:14px;height:3px;background:var(--red);margin-top:4px}
.hd.center{left:0;right:0;text-align:center}
.hd.center::after{margin-left:auto;margin-right:auto}
.hd.white{color:#fff}
.tiny{font-size:4.6px;line-height:1.45;color:var(--muted)}
.small{font-size:5.4px;line-height:1.5;color:var(--muted)}
.white-t{color:#fff}
.pill{position:absolute;border-radius:20px;font-size:5.5px;text-align:center;font-weight:600}
.card{position:absolute;border-radius:4px;color:#fff;text-align:center;padding:4px 4px}
.card b{display:block;font-size:5px;margin:3px 0 2px}
.card p{font-size:4.2px;line-height:1.4;opacity:.9}
.bg-red{background:var(--red)}.bg-navy{background:var(--navy)}.bg-gray{background:var(--gray)}.bg-deep{background:var(--navy-deep)}
table{border-collapse:collapse;width:100%}
td,th{font-size:4.6px;text-align:center;padding:3px 2px}
th{font-weight:600}
</style>
</head>
<body>
<main class="deck">

<!-- 1 cover -->
<section class="slide">
  <div class="photo photo-navy" style="inset:0" role="img" aria-label="Dark blue photo of a person using a tablet"></div>
  <div class="abs" style="top:32px;left:0;right:0;text-align:center"><span class="brand light" style="font-size:10px"><span class="dot"></span>Ledger Lanternfox</span></div>
  <div class="pill" style="top:52px;left:122px;width:143px;background:rgba(255,255,255,.15);color:#cfd8e8;font-weight:400;padding:2px 0">www.websitename.com</div>
  <div class="abs" style="top:70px;left:0;right:0;text-align:center;color:#fff;font-weight:600;font-size:24px;line-height:1">Presentation<br>Title Goes Here</div>
  <div class="abs" style="top:122px;left:0;right:0;text-align:center;color:#dfe6f2;font-size:8px">Sub Title Goes Here</div>
  <div class="pill" style="top:176px;left:147px;width:93px;background:var(--red);color:#fff;padding:2px 0">Oct 2021</div>
</section>

<!-- 2 -->
<section class="slide">
  <div class="photo photo-navy" style="left:0;top:0;right:0;height:185px" role="img" aria-label="Blue tinted office photo"></div>
  <div class="abs" style="left:20px;top:70px;color:#fff;font-weight:500;font-size:20px;line-height:1.15">TITLE OF<br>PRESENTATION</div>
  <div class="abs tiny white-t" style="left:20px;top:138px">Here is a place for Credentials<br>Date: 2021 March</div>
  <div class="abs" style="left:10px;top:194px"><span class="brand" style="font-size:8px"><span class="dot"></span>Ledger Lanternfox</span></div>
  <div class="abs" style="right:14px;top:199px;font-size:5.5px;font-weight:600;color:var(--navy)">Presenter Name</div>
</section>

<!-- 3 -->
<section class="slide">
  <div class="photo photo-navy" style="inset:0" role="img" aria-label="Blue tinted server room photo"></div>
  <div class="abs" style="left:24px;top:60px"><span class="brand light" style="font-size:7px"><span class="dot"></span>Ledger Lanternfox</span></div>
  <div class="abs" style="left:24px;top:82px;color:#fff;font-weight:500;font-size:20px;line-height:1.15">TITLE OF<br>PRESENTATION</div>
  <div class="abs tiny white-t" style="left:24px;top:152px">Here is A place for Credentials<br>Date: 2021 March</div>
</section>

<!-- 4 -->
<section class="slide">
  <div class="photo photo-gray" style="inset:0" role="img" aria-label="Photo of a laptop on a desk seen from above"></div>
  <div class="abs" style="left:40px;top:48px"><span class="brand light" style="font-size:17px"><span class="dot"></span>Ledger Lanternfox</span></div>
  <svg class="abs" style="left:0;top:0" width="387" height="217" aria-hidden="true"><polygon points="125,112 387,112 387,168 95,168" fill="#e8262c"/></svg>
  <div class="abs" style="left:150px;right:10px;top:120px;color:#fff;font-weight:600;font-size:17px;line-height:1;text-align:center">Presentation<br>Title Goes Here</div>
</section>

<!-- 5 -->
<section class="slide navy">
  <div class="abs" style="top:20px;left:0;right:0;text-align:center"><span class="brand light" style="font-size:9px"><span class="dot"></span>Ledger Lanternfox</span></div>
</section>

<!-- 6 -->
<section class="slide">
  <div class="abs" style="top:22px;left:0;right:0;text-align:center"><span class="brand" style="font-size:9px"><span class="dot"></span>Ledger Lanternfox</span></div>
</section>

<!-- 7 -->
<section class="slide">
  <div class="abs" style="left:25px;top:44px"><span class="brand" style="font-size:9px"><span class="dot"></span>Ledger Lanternfox</span></div>
  <div class="abs" style="left:24px;top:82px;color:var(--navy);font-weight:600;font-size:24px;line-height:1">Presentation<br>Title Goes Here</div>
  <div class="abs" style="left:24px;top:132px;color:var(--red);font-size:8px">Sub Title Goes Here</div>
  <div class="pill" style="left:20px;top:172px;width:116px;background:var(--red);color:#fff;font-weight:400;padding:2px 0">www.websitename.com</div>
</section>

<!-- 8 about -->
<section class="slide">
  <div class="corner"></div><div class="side">Ledger Lanternfox</div><div class="pg">8</div>
  <div class="photo" style="left:48px;top:50px;width:84px;height:84px;border-radius:50%;background:linear-gradient(135deg,#8a8a8a,#2e2e2e)" role="img" aria-label="Portrait photo of the presenter"></div>
  <div class="abs tiny" style="left:55px;top:146px;color:var(--navy)">● Here is a place for text<br><br>● Here is a place for text<br><br>● Here is a place for text</div>
  <div class="abs" style="left:159px;top:30px;bottom:20px;width:1px;background:var(--line)"></div>
  <div class="abs" style="left:170px;top:30px;color:var(--red);font-size:8px">Manager</div>
  <div class="abs" style="left:170px;top:40px;color:var(--navy);font-weight:600;font-size:14px">Name, Last Name</div>
  <div class="abs tiny" style="left:170px;top:70px;width:200px;text-align:justify"><span style="color:var(--red);font-weight:600">Lorem ipsum dolor sit amet, consectetur adipiscing elit,</span> sed do eiusmod tempor incididunt ut labore et dolore magna aliqua. Lorem ipsum dolor sit amet, consectetur adipiscing elit, sed do eiusmod tempor incididunt ut labore et dolore magna aliqua ut enim ad minim veniam nisi ut aliquip.<br><br>Lorem ipsum dolor sit amet, consectetur adipiscing elit. Lorem ipsum dolor sit amet, consectetur adipiscing elit, sed do eiusmod tempor incididunt ut labore et dolore magna aliqua. Lorem ipsum dolor sit amet, sed do eiusmod tempor incididunt ut labore et dolore magna aliqua ut enim ad minim veniam, quis nostrud exercitation.</div>
</section>

<!-- 9 welcome -->
<section class="slide">
  <div class="corner"></div><div class="side">Ledger Lanternfox</div><div class="pg">9</div>
  <div class="photo" style="left:45px;top:55px;width:110px;height:110px;border-radius:12px;background:linear-gradient(135deg,#8a8a8a,#2a2a2a)" role="img" aria-label="Portrait photo of the presenter"></div>
  <div class="pill" style="left:70px;top:150px;width:98px;background:var(--red);color:#fff;padding:3px 0;font-size:7px">Your Name</div>
  <div class="abs" style="right:18px;top:34px;color:var(--navy);font-weight:600;font-size:15px">Welcome Message</div>
  <div class="abs tiny" style="left:190px;top:76px;width:180px;text-align:justify">Lorem ipsum dolor sit amet consectetur adipiscing elit, sed do eiusmod tempor incididunt ut labore et dolore magna aliqua lorem ipsum dolor sit amet, consectetur adipiscing elit sed do eiusmod tempor.<br><br>Lorem ipsum dolor sit amet, consectetur adipiscing elit, sed do eiusmod tempor incididunt ut labore et dolore magna aliqua. Lorem ipsum dolor sit amet, consectetur adipiscing elit, sed do eiusmod tempor incididunt ut labore et dolore magna aliqua. Lorem ipsum dolor sit amet, consectetur adipiscing elit, sed do eiusmod tempor incididunt ut labore et dolore magna aliqua.</div>
</section>

<!-- 10 agenda -->
<section class="slide">
  <div class="corner"></div><div class="side">Ledger Lanternfox</div><div class="pg">10</div>
  <div class="abs bg-navy" style="left:237px;top:0;right:0;height:95px"></div>
  <div class="abs" style="left:44px;top:74px;color:var(--navy);font-weight:600;font-size:15px;line-height:1.15">Here Goes<br>Title Of Your<br>Agenda</div>
  <div class="abs" style="left:44px;top:135px;color:var(--red);font-size:6.5px">Here Goes A Short Subtitle</div>
  <ol class="abs" style="left:187px;top:32px;width:170px;height:160px;background:#fff;box-shadow:0 2px 10px rgba(0,0,0,.12);padding:14px 10px 0 32px;font-size:6.8px;color:var(--navy);line-height:2.85">
    <li>Lorem ipsum dolor sit amet</li><li>Lorem ipsum dolor sit amet</li><li>Lorem ipsum dolor sit amet</li><li>Lorem ipsum dolor sit amet</li><li>Lorem ipsum dolor sit amet</li><li>Lorem ipsum dolor sit amet</li><li>Lorem ipsum dolor sit amet</li>
  </ol>
</section>

<!-- 11 -->
<section class="slide">
  <div class="corner"></div><div class="side">Ledger Lanternfox</div><div class="pg">11</div>
  <div class="hd" style="left:34px;top:22px">Title And Body Slide</div>
</section>

<!-- 12 -->
<section class="slide">
  <div class="corner"></div><div class="side">Ledger Lanternfox</div><div class="pg">12</div>
  <div class="hd" style="left:34px;top:22px">Title And Body Slide</div>
</section>

<!-- 13 -->
<section class="slide navy">
  <div class="corner" style="border-color:#fff"></div><div class="side" style="color:#fff">Ledger Lanternfox</div><div class="pg" style="color:#cfd8e8">13</div>
  <div class="hd white" style="left:34px;top:22px">Title And Body Slide</div>
</section>

<!-- 14 -->
<section class="slide">
  <div class="corner"></div><div class="side">Ledger Lanternfox</div><div class="pg">14</div>
  <div class="hd" style="left:34px;top:22px">Title And Body Slide</div>
  <div class="abs tiny" style="left:38px;top:68px;width:325px;text-align:justify">Lorem ipsum dolor sit amet, consectetur adipiscing elit, sed do eiusmod tempor incididunt ut labore et dolore magna aliqua. Lorem ipsum dolor sit amet, consectetur adipiscing elit, sed do eiusmod tempor incididunt ut labore et dolore magna aliqua. Ut enim ad minim veniam, quis nostrud exercitation ullamco laboris nisi ut aliquip.<br><br>Lorem ipsum dolor sit amet, consectetur adipiscing elit. Lorem ipsum dolor sit amet, consectetur adipiscing elit, sed do eiusmod tempor incididunt ut labore et dolore magna aliqua. Lorem ipsum dolor sit amet, consectetur adipiscing elit, sed do eiusmod tempor incididunt ut labore et dolore magna aliqua, ut enim ad minim veniam.<br><br>Lorem ipsum dolor sit amet, consectetur adipiscing elit, sed do eiusmod tempor incididunt ut labore et dolore magna aliqua. Lorem ipsum dolor sit amet, consectetur adipiscing elit, sed do eiusmod tempor incididunt ut labore et dolore magna aliqua. Lorem ipsum dolor sit amet, consectetur adipiscing elit, sed do eiusmod tempor incididunt ut labore et dolore magna aliqua lorem ipsum dolor sit amet, quis nostrud exercitation ullamco laboris nisi ut aliquip ex ea commodo.</div>
</section>

<!-- 15 break -->
<section class="slide">
  <div class="abs" style="left:14px;top:40px;color:#e3e8f1;font-weight:300;font-size:62px;line-height:1">01</div>
  <div class="abs" style="left:36px;top:66px;color:var(--navy);font-weight:300;font-size:30px;line-height:1">Slide<br>Break</div>
  <div class="abs tiny" style="left:36px;top:134px;width:160px">Lorem ipsum dolor sit amet, consectetur adipiscing elit, sed do eiusmod tempor incididunt ut labore et dolore magna aliqua. Lorem ipsum dolor sit amet, consectetur adipiscing elit, sed do eiusmod tempor incididunt ut labore et dolore magna aliqua.</div>
  <div class="abs" style="left:220px;top:98px"><span class="brand" style="font-size:13px;color:var(--navy)"><span class="dot" style="background:var(--navy)"></span>Ledger Lanternfox</span></div>
  <div class="abs bg-red" style="left:0;right:0;bottom:0;height:8px"></div>
</section>

<!-- 16 break navy -->
<section class="slide navy">
  <div class="abs" style="left:22px;top:40px;color:#2d5296;font-weight:300;font-size:62px;line-height:1">01</div>
  <div class="abs" style="left:44px;top:66px;color:#fff;font-weight:300;font-size:30px;line-height:1">Slide<br>Break</div>
  <div class="abs tiny white-t" style="left:44px;top:134px;width:160px">Lorem ipsum dolor sit amet, consectetur adipiscing elit, sed do eiusmod tempor incididunt ut labore et dolore magna aliqua. Lorem ipsum dolor sit amet, consectetur adipiscing elit, sed do eiusmod tempor incididunt ut labore et dolore magna aliqua.</div>
</section>

<!-- 17 demo -->
<section class="slide">
  <div class="photo photo-navy" style="inset:0" role="img" aria-label="Blue tinted photo of a person at a laptop"></div>
  <div class="abs" style="left:104px;top:20px;width:178px;height:178px;border-radius:50%;border:1.5px solid rgba(255,255,255,.8)"></div>
  <div class="abs" style="left:0;right:0;top:48px;text-align:center;color:var(--red);font-weight:600;font-size:16px">DEMO</div>
  <div class="abs small white-t" style="left:120px;width:147px;top:76px;text-align:center">Lorem ipsum dolor sit amet, consectetur adipiscing elit, sed do eiusmod tempor incididunt ut labore et dolore magna aliqua. Lorem ipsum dolor sit amet, consectetur adipiscing elit, sed do eiusmod tempor incididunt ut magna aliqua. Lorem ipsum dolor sit amet, consectetur adipiscing elit, sed do eiusmod tempor incididunt ut labore et dolore magna aliqua. Lorem ipsum dolor sit amet.</div>
</section>

<!-- 18 demo navy -->
<section class="slide navy">
  <div class="abs" style="left:96px;top:12px;width:194px;height:194px;border-radius:50%;background:var(--navy-dark)"></div>
  <div class="abs" style="left:104px;top:20px;width:178px;height:178px;border-radius:50%;border:1.5px solid rgba(255,255,255,.8)"></div>
  <div class="abs" style="left:0;right:0;top:48px;text-align:center;color:#fff;font-weight:600;font-size:16px">DEMO</div>
  <div class="abs small white-t" style="left:120px;width:147px;top:76px;text-align:center">Lorem ipsum dolor sit amet, consectetur adipiscing elit, sed do eiusmod tempor incididunt ut labore et dolore magna aliqua. Lorem ipsum dolor sit amet, consectetur adipiscing elit, sed do eiusmod tempor incididunt ut magna aliqua. Lorem ipsum dolor sit amet, consectetur adipiscing elit, sed do eiusmod tempor incididunt ut labore et dolore magna aliqua. Lorem ipsum dolor sit amet.</div>
</section>

<!-- 19 demo brand -->
<section class="slide">
  <div class="photo photo-navy" style="inset:0" role="img" aria-label="Blue tinted photo of hands typing on a laptop"></div>
  <div class="abs" style="left:28px;top:104px"><span class="brand light" style="font-size:8px"><span class="dot"></span>Ledger Lanternfox</span></div>
  <div class="abs bg-red" style="left:146px;top:64px;width:2px;height:90px"></div>
  <div class="pill" style="left:158px;top:66px;width:74px;background:var(--red);color:#fff;font-size:11px;padding:1px 0;text-align:left;padding-left:10px">DEMO</div>
  <div class="abs white-t" style="left:160px;top:90px;width:205px;font-size:6.8px;line-height:1.35">Lorem ipsum dolor sit amet, consectetur adipiscing elit, sed do eiusmod tempor incididunt ut labore et dolore magna aliqua. Lorem ipsum dolor sit amet, consectetur adipiscing elit, sed do eiusmod tempor incididunt ut labore et dolore magna aliqua.</div>
</section>

<!-- 20 pic and text -->
<section class="slide">
  <div class="corner"></div><div class="side">Ledger Lanternfox</div><div class="pg">20</div>
  <div class="hd" style="left:38px;top:62px;font-size:18px">Pic And Text</div>
  <div class="abs tiny" style="left:38px;top:100px;width:134px;text-align:justify;font-size:5px">Lorem ipsum dolor sit amet, consectetur adipiscing elit, sed do eiusmod tempor incididunt ut labore et dolore magna aliqua. Lorem ipsum dolor sit amet, consectetur adipiscing elit, sed do eiusmod tempor incididunt ut labore et dolore magna aliqua. Ut enim ad minim veniam, quis nostrud exercitation ullamco laboris nisi ut aliquip.</div>
  <div class="abs bg-red" style="left:190px;top:28px;width:78px;height:78px"></div>
  <div class="photo photo-gray" style="left:210px;top:48px;width:160px;height:140px;box-shadow:0 4px 10px rgba(0,0,0,.2)" role="img" aria-label="Photo of a person working at a computer keyboard"></div>
</section>

<!-- 21 quote -->
<section class="slide">
  <div class="photo" style="left:0;top:0;width:168px;bottom:0;background:linear-gradient(180deg,#8c9bb0,#39404d)" role="img" aria-label="Photo of a hiker standing on a mountain top"></div>
  <div class="abs" style="left:190px;top:68px;width:175px;color:var(--navy);font-weight:500;font-size:8.5px;line-height:1.3"><span style="display:block;width:12px;height:2px;background:var(--red);margin-bottom:4px"></span>Success is not only what you achieve in your life, but also what you inspire in the lives of others</div>
  <div class="abs bg-navy" style="left:110px;right:0;bottom:0;height:74px"></div>
  <div class="abs tiny white-t" style="left:112px;top:160px;width:84px;font-size:4.2px"><b style="font-size:5.4px">Lorem ipsum dolor</b><br>Lorem ipsum dolor sit amet, consectetur adipiscing elit, sed do eiusmod tempor</div>
  <div class="abs tiny white-t" style="left:205px;top:160px;width:84px;font-size:4.2px"><b style="font-size:5.4px">Lorem ipsum dolor</b><br>Lorem ipsum dolor sit amet, consectetur adipiscing elit, sed do eiusmod tempor</div>
  <div class="abs tiny white-t" style="left:300px;top:160px;width:84px;font-size:4.2px"><b style="font-size:5.4px">Lorem ipsum dolor</b><br>Lorem ipsum dolor sit amet, consectetur adipiscing elit, sed do eiusmod tempor</div>
</section>

<!-- 22 awesome text -->
<section class="slide">
  <div class="corner"></div><div class="side">Ledger Lanternfox</div><div class="pg">22</div>
  <div class="abs bg-navy" style="left:24px;top:0;right:0;height:108px"></div>
  <div class="hd center white" style="left:24px;top:32px;font-size:15px">Here Add Awesome Text</div>
  <div class="abs" style="left:24px;right:0;top:88px;display:flex;justify-content:space-around">
    <div style="width:100px;text-align:center"><svg width="40" height="40" aria-hidden="true"><circle cx="20" cy="20" r="19" fill="#e8262c" stroke="#fff" stroke-width="2"/><circle cx="20" cy="20" r="8" fill="none" stroke="#fff" stroke-width="1.5"/><circle cx="20" cy="20" r="3" fill="#fff"/></svg><div style="font-size:6.5px;font-weight:600;margin:4px 0 2px">Project name</div><div class="tiny">Lorem ipsum dolor sit amet, nec an dictas equidem appellantur ut has commune accommodare. Mea illum, ludus solet idipro.</div></div>
    <div style="width:100px;text-align:center"><svg width="40" height="40" aria-hidden="true"><circle cx="20" cy="20" r="19" fill="#e8262c" stroke="#fff" stroke-width="2"/><path d="M14 26 L26 14 M20 14 L26 14 L26 20" stroke="#fff" stroke-width="1.6" fill="none"/></svg><div style="font-size:6.5px;font-weight:600;margin:4px 0 2px">Project name</div><div class="tiny">Lorem ipsum dolor sit amet, nec an dictas equidem appellantur ut has commune accommodare. Mea illum, ludus solet idipro.</div></div>
    <div style="width:100px;text-align:center"><svg width="40" height="40" aria-hidden="true"><circle cx="20" cy="20" r="19" fill="#e8262c" stroke="#fff" stroke-width="2"/><rect x="13" y="21" width="3" height="6" fill="#fff"/><rect x="18.5" y="16" width="3" height="11" fill="#fff"/><rect x="24" y="12" width="3" height="15" fill="#fff"/></svg><div style="font-size:6.5px;font-weight:600;margin:4px 0 2px">Project name</div><div class="tiny">Lorem ipsum dolor sit amet, nec an dictas equidem appellantur ut has commune accommodare. Mea illum, ludus solet idipro.</div></div>
  </div>
</section>

<!-- 23 3 columns -->
<section class="slide">
  <div class="corner"></div><div class="side">Ledger Lanternfox</div><div class="pg">23</div>
  <div class="hd center" style="top:26px;font-size:15px">3 Columns Slide</div>
  <svg class="abs" style="left:87px;top:64px" width="220" height="26" aria-hidden="true"><circle cx="13" cy="13" r="8" fill="none" stroke="#e8262c" stroke-width="1.4"/><circle cx="112" cy="13" r="8" fill="none" stroke="#1c3f7f" stroke-width="1.4"/><circle cx="112" cy="13" r="3" fill="#1c3f7f"/><circle cx="211" cy="13" r="8" fill="none" stroke="#7b7b7b" stroke-width="1.4"/></svg>
  <div class="card bg-red" style="left:53px;top:88px;width:89px;height:75px"><b>Project name here</b><p>Lorem ipsum dolor sit amet, nec an dictas equidem appellantur, ut has commune accommodare. Mea illum, ludus solet idipro.</p></div>
  <div class="card bg-navy" style="left:152px;top:88px;width:89px;height:75px"><b>Project name here</b><p>Lorem ipsum dolor sit amet, nec an dictas equidem appellantur, ut has commune accommodare. Mea illum, ludus solet idipro.</p></div>
  <div class="card bg-gray" style="left:251px;top:88px;width:89px;height:75px"><b>Project name here</b><p>Lorem ipsum dolor sit amet, nec an dictas equidem appellantur, ut has commune accommodare. Mea illum, ludus solet idipro.</p></div>
</section>

<!-- 24 4 columns -->
<section class="slide">
  <div class="corner"></div><div class="side">Ledger Lanternfox</div><div class="pg">24</div>
  <div class="hd center" style="top:20px;font-size:15px">4 Column Slide</div>
  <svg class="abs" style="left:56px;top:58px" width="300" height="24" aria-hidden="true"><circle cx="16" cy="12" r="8" fill="none" stroke="#e8262c" stroke-width="1.4"/><circle cx="102" cy="12" r="8" fill="none" stroke="#1c3f7f" stroke-width="1.4"/><circle cx="188" cy="12" r="8" fill="none" stroke="#12295a" stroke-width="1.4"/><circle cx="274" cy="12" r="8" fill="none" stroke="#7b7b7b" stroke-width="1.4"/></svg>
  <div class="card bg-red" style="left:32px;top:80px;width:81px;height:104px"><b>Project name here</b><p>Lorem ipsum dolor sit amet, nec an dictas equidem appellantur, ut has commune accommodare. Mea illum, ludus solet idipro lorem ipsum dolor sit amet nec an.</p></div>
  <div class="card bg-navy" style="left:118px;top:80px;width:81px;height:104px"><b>Project name here</b><p>Lorem ipsum dolor sit amet, nec an dictas equidem appellantur, ut has commune accommodare. Mea illum, ludus solet idipro lorem ipsum dolor sit amet nec an.</p></div>
  <div class="card bg-deep" style="left:204px;top:80px;width:81px;height:104px"><b>Project name here</b><p>Lorem ipsum dolor sit amet, nec an dictas equidem appellantur, ut has commune accommodare. Mea illum, ludus solet idipro lorem ipsum dolor sit amet nec an.</p></div>
  <div class="card bg-gray" style="left:290px;top:80px;width:81px;height:104px"><b>Project name here</b><p>Lorem ipsum dolor sit amet, nec an dictas equidem appellantur, ut has commune accommodare. Mea illum, ludus solet idipro lorem ipsum dolor sit amet nec an.</p></div>
</section>

<!-- 25 5 columns -->
<section class="slide">
  <div class="corner"></div><div class="side">Ledger Lanternfox</div><div class="pg">25</div>
  <div class="hd center" style="top:24px;font-size:15px">5 Column Slide</div>
  <div class="card bg-navy" style="left:53px;top:65px;width:90px;height:58px"><b>Project name here</b><p>Lorem ipsum dolor sit amet, nec an dictas equidem appellantur, ut has commune accommodare. Mea illum, ludus solet idipro.</p></div>
  <div class="card bg-navy" style="left:152px;top:65px;width:90px;height:58px"><b>Project name here</b><p>Lorem ipsum dolor sit amet, nec an dictas equidem appellantur, ut has commune accommodare. Mea illum, ludus solet idipro.</p></div>
  <div class="card bg-navy" style="left:251px;top:65px;width:90px;height:58px"><b>Project name here</b><p>Lorem ipsum dolor sit amet, nec an dictas equidem appellantur, ut has commune accommodare. Mea illum, ludus solet idipro.</p></div>
  <div class="card bg-navy" style="left:100px;top:130px;width:90px;height:58px"><b>Project name here</b><p>Lorem ipsum dolor sit amet, nec an dictas equidem appellantur, ut has commune accommodare. Mea illum, ludus solet idipro.</p></div>
  <div class="card bg-navy" style="left:199px;top:130px;width:90px;height:58px"><b>Project name here</b><p>Lorem ipsum dolor sit amet, nec an dictas equidem appellantur, ut has commune accommodare. Mea illum, ludus solet idipro.</p></div>
</section>

<!-- 26 screenshot -->
<section class="slide">
  <div class="corner"></div><div class="side">Ledger Lanternfox</div><div class="pg">26</div>
  <svg class="abs" style="left:0;top:0" width="387" height="217" aria-hidden="true"><polygon points="24,0 176,0 290,217 24,217" fill="#1c3f7f"/></svg>
  <div class="abs" style="left:44px;top:68px;color:#fff;font-weight:600;font-size:15px;line-height:1.15">A Place for<br>Screenshot<span style="display:block;width:14px;height:3px;background:var(--red);margin-top:5px"></span></div>
  <div class="abs tiny white-t" style="left:44px;top:126px;width:115px">Lorem ipsum dolor sit amet consectetur adipiscing elit, sed do eiusmod tempor ela bela on lipon elorem dolor sin ler li.</div>
  <div class="abs" style="left:176px;top:50px;width:196px;height:122px;background:#1d1d1d;border-radius:5px;padding:5px"><div style="width:100%;height:100%;background:#9b9b9b;display:flex;align-items:center;justify-content:center;color:#fff;font-size:6px;font-weight:600">HERE YOU CAN ADD A SCREENSHOT</div></div>
  <div class="abs" style="left:160px;top:172px;width:228px;height:6px;background:linear-gradient(#d7d7d7,#9a9a9a);border-radius:0 0 6px 6px"></div>
</section>

<!-- 27 6 columns -->
<section class="slide">
  <div class="corner"></div><div class="side">Ledger Lanternfox</div><div class="pg">27</div>
  <div class="hd center" style="top:22px;font-size:15px">6 Columns Slide</div>
  <div class="abs" style="left:40px;top:60px;width:330px;display:grid;grid-template-columns:1fr 1fr;column-gap:20px;row-gap:10px">
    <div style="display:flex;gap:12px"><svg width="16" height="16" aria-hidden="true"><rect x="2" y="2" width="12" height="12" rx="2" fill="none" stroke="#1c3f7f" stroke-width="1.2"/></svg><div class="tiny"><b style="color:var(--ink)">Project name</b><br>Lorem ipsum dolor sit amet, nec an dictas equidem appellantur, ut has commune accommodare. Mea illum, ludus solet idipro.</div></div>
    <div style="display:flex;gap:12px"><svg width="16" height="16" aria-hidden="true"><rect x="2" y="2" width="12" height="12" rx="2" fill="none" stroke="#1c3f7f" stroke-width="1.2"/></svg><div class="tiny"><b style="color:var(--ink)">Project name</b><br>Lorem ipsum dolor sit amet, nec an dictas equidem appellantur, ut has commune accommodare. Mea illum, ludus solet idipro.</div></div>
    <div style="display:flex;gap:12px"><svg width="16" height="16" aria-hidden="true"><path d="M2 14 L7 8 L10 11 L14 4" stroke="#1c3f7f" stroke-width="1.2" fill="none"/></svg><div class="tiny"><b style="color:var(--ink)">Project name</b><br>Lorem ipsum dolor sit amet, nec an dictas equidem appellantur, ut has commune accommodare. Mea illum, ludus solet idipro.</div></div>
    <div style="display:flex;gap:12px"><svg width="16" height="16" aria-hidden="true"><path d="M2 14 L7 8 L10 11 L14 4" stroke="#1c3f7f" stroke-width="1.2" fill="none"/></svg><div class="tiny"><b style="color:var(--ink)">Project name</b><br>Lorem ipsum dolor sit amet, nec an dictas equidem appellantur, ut has commune accommodare. Mea illum, ludus solet idipro.</div></div>
    <div style="display:flex;gap:12px"><svg width="16" height="16" aria-hidden="true"><circle cx="8" cy="8" r="6" fill="none" stroke="#1c3f7f" stroke-width="1.2"/></svg><div class="tiny"><b style="color:var(--ink)">Project name</b><br>Lorem ipsum dolor sit amet, nec an dictas equidem appellantur, ut has commune accommodare. Mea illum, ludus solet idipro.</div></div>
    <div style="display:flex;gap:12px"><svg width="16" height="16" aria-hidden="true"><circle cx="8" cy="8" r="6" fill="none" stroke="#1c3f7f" stroke-width="1.2"/></svg><div class="tiny"><b style="color:var(--ink)">Project name</b><br>Lorem ipsum dolor sit amet, nec an dictas equidem appellantur, ut has commune accommodare. Mea illum, ludus solet idipro.</div></div>
  </div>
</section>

<!-- 28 table ticks -->
<section class="slide">
  <div class="corner"></div><div class="side">Ledger Lanternfox</div><div class="pg">28</div>
  <div class="hd center" style="top:20px;font-size:15px">Table Slide</div>
  <div class="abs" style="left:30px;top:60px;width:340px">
    <table>
      <tr><th style="width:90px"></th><th class="bg-red" style="color:#fff">Your Text Here</th><th class="bg-red" style="color:#fff">Your Text Here</th><th class="bg-red" style="color:#fff">Your Text Here</th><th class="bg-red" style="color:#fff">Your Text Here</th></tr>
      <tr><th class="bg-navy" style="color:#fff">You can replace this text</th><td>1097</td><td style="color:var(--navy)">✔</td><td>3270</td><td>1350</td></tr>
      <tr><th class="bg-navy" style="color:#fff">You can replace this text</th><td>3803</td><td>✖</td><td>5271</td><td>2803</td></tr>
      <tr><th class="bg-navy" style="color:#fff">You can replace this text</th><td>2969</td><td style="color:var(--navy)">✔</td><td>1071</td><td>2969</td></tr>
      <tr><th class="bg-navy" style="color:#fff">You can replace this text</th><td>3110</td><td>✖</td><td>1931</td><td>3110</td></tr>
      <tr><th class="bg-navy" style="color:#fff">You can replace this text</th><td>2300</td><td style="color:var(--navy)">✔</td><td>3871</td><td>2300</td></tr>
      <tr><th class="bg-navy" style="color:#fff">You can replace this text</th><td>2658</td><td>✖</td><td>1931</td><td>2658</td></tr>
      <tr><th class="bg-navy" style="color:#fff">You can replace this text</th><td>1999</td><td style="color:var(--navy)">✔</td><td>6001</td><td>1999</td></tr>
    </table>
  </div>
</section>

<!-- 29 table card -->
<section class="slide">
  <div class="corner"></div><div class="side">Ledger Lanternfox</div><div class="pg">29</div>
  <div class="abs bg-navy" style="left:24px;top:0;width:226px;height:205px"></div>
  <div class="abs" style="left:40px;top:104px;color:#fff;font-weight:600;font-size:15px">Table Slide<span style="display:block;width:14px;height:3px;background:var(--red);margin-top:5px"></span></div>
  <div class="abs" style="left:160px;top:38px;width:210px;height:150px;background:#fff;box-shadow:0 2px 10px rgba(0,0,0,.15);padding:6px 8px">
    <table>
      <tr class="bg-navy" style="color:#fff"><th>Text</th><th>Text</th><th>Text</th><th>Text</th><th>Text</th></tr>
      <tr><th>Data</th><td>Data</td><td>Data</td><td>Data</td><td>Data</td></tr>
      <tr><th>Data</th><td>Data</td><td>Data</td><td>Data</td><td>Data</td></tr>
      <tr><th>Data</th><td>Data</td><td>Data</td><td>Data</td><td>Data</td></tr>
      <tr><th>Data</th><td>Data</td><td>Data</td><td>Data</td><td>Data</td></tr>
      <tr><th>Data</th><td>Data</td><td>Data</td><td>Data</td><td>Data</td></tr>
      <tr><th>Data</th><td>Data</td><td>Data</td><td>Data</td><td>Data</td></tr>
    </table>
  </div>
</section>

<!-- 30 table -->
<section class="slide">
  <div class="corner"></div><div class="side">Ledger Lanternfox</div><div class="pg">30</div>
  <div class="hd center" style="top:20px;font-size:15px">Table Slide</div>
  <div class="abs" style="left:40px;top:60px;width:322px">
    <table>
      <tr class="bg-navy" style="color:#fff"><th>Text</th><th>Text</th><th>Text</th><th>Text</th><th>Text</th></tr>
      <tr style="border-bottom:1px solid var(--line)"><th>Data</th><td>Data</td><td>Data</td><td>Data</td><td>Data</td></tr>
      <tr style="border-bottom:1px solid var(--line)"><th>Data</th><td>Data</td><td>Data</td><td>Data</td><td>Data</td></tr>
      <tr style="border-bottom:1px solid var(--line)"><th>Data</th><td>Data</td><td>Data</td><td>Data</td><td>Data</td></tr>
      <tr style="border-bottom:1px solid var(--line)"><th>Data</th><td>Data</td><td>Data</td><td>Data</td><td>Data</td></tr>
      <tr style="border-bottom:1px solid var(--line)"><th>Data</th><td>Data</td><td>Data</td><td>Data</td><td>Data</td></tr>
      <tr style="border-bottom:1px solid var(--navy)"><th>Data</th><td>Data</td><td>Data</td><td>Data</td><td>Data</td></tr>
    </table>
  </div>
</section>

<!-- 31 smart art -->
<section class="slide">
  <div class="corner"></div><div class="side">Ledger Lanternfox</div><div class="pg">31</div>
  <div class="hd" style="left:34px;top:22px;font-size:15px">Smart Art Slide</div>
  <div class="abs" style="left:36px;top:72px;width:150px;display:flex;flex-direction:column;gap:14px">
    <div style="display:flex;gap:8px"><svg width="14" height="14" aria-hidden="true"><circle cx="7" cy="7" r="5.5" fill="none" stroke="#1c3f7f" stroke-width="1.1"/></svg><div class="tiny"><b style="color:var(--ink)">Lorem ipsum dolor</b><br>Lorem ipsum dolor sit amet, consectetur adipiscing elit, sed do eiusmod tempor ala bela on lipon dolor ler li.</div></div>
    <div style="display:flex;gap:8px"><svg width="14" height="14" aria-hidden="true"><circle cx="7" cy="7" r="5.5" fill="none" stroke="#1c3f7f" stroke-width="1.1"/></svg><div class="tiny"><b style="color:var(--ink)">Lorem ipsum dolor</b><br>Lorem ipsum dolor sit amet, consectetur adipiscing elit, sed do eiusmod tempor ala bela on lipon dolor ler li.</div></div>
    <div style="display:flex;gap:8px"><svg width="14" height="14" aria-hidden="true"><circle cx="7" cy="7" r="5.5" fill="none" stroke="#1c3f7f" stroke-width="1.1"/></svg><div class="tiny"><b style="color:var(--ink)">Lorem ipsum dolor</b><br>Lorem ipsum dolor sit amet, consectetur adipiscing elit, sed do eiusmod tempor ala bela on lipon dolor ler li.</div></div>
  </div>
  <svg class="abs" style="left:208px;top:42px" width="164" height="150" aria-hidden="true">
    <polygon points="82,4 122,72 42,72" fill="#1c3f7f"/>
    <polygon points="40,78 80,78 80,146 2,146" fill="#e8262c"/>
    <polygon points="84,78 124,78 162,146 84,146" fill="#7b7b7b"/>
  </svg>
  <div class="abs" style="left:270px;top:74px;width:40px;text-align:center;color:#fff;font-size:5px;font-weight:600">Project name<div style="font-size:3.8px;font-weight:400;opacity:.85">Lorem ipsum dolor sit amet nec an dictas equidem</div></div>
  <div class="abs" style="left:228px;top:134px;width:60px;text-align:center;color:#fff;font-size:5px;font-weight:600">Project name<div style="font-size:3.8px;font-weight:400;opacity:.85">Lorem ipsum dolor sit amet nec an dictas equidem appellantur</div></div>
  <div class="abs" style="left:293px;top:134px;width:60px;text-align:center;color:#fff;font-size:5px;font-weight:600">Project name<div style="font-size:3.8px;font-weight:400;opacity:.85">Lorem ipsum dolor sit amet nec an dictas equidem appellantur</div></div>
</section>

<!-- 32 quotes -->
<section class="slide">
  <div class="corner"></div><div class="side">Ledger Lanternfox</div><div class="pg">32</div>
  <div class="hd center" style="top:20px;font-size:15px">Here is Quotes</div>
  <div class="abs" style="left:38px;top:58px;width:150px">
    <div style="color:var(--red);font-size:30px;font-weight:700;line-height:.8">”</div>
    <div class="small" style="margin-top:6px">Lorem ipsum dolor sit amet, consectetur adipiscing elit, sed do eiusmod tempor incididunt ut labore et dolore magna aliqua. Lorem ipsum dolor sit amet, consectetur adipiscing elit.</div>
    <div style="display:flex;align-items:center;gap:6px;margin-top:12px"><span style="width:18px;height:18px;border-radius:50%;background:#d6d6d6;display:inline-block" role="img" aria-label="Avatar placeholder"></span><span style="font-size:5.5px;color:var(--navy);font-weight:600">Your Name<br><span style="font-weight:400;color:var(--muted)">Founder</span></span></div>
  </div>
  <div class="abs" style="left:216px;top:58px;width:150px">
    <div style="color:var(--navy);font-size:30px;font-weight:700;line-height:.8">”</div>
    <div class="small" style="margin-top:6px">Lorem ipsum dolor sit amet, consectetur adipiscing elit, sed do eiusmod tempor incididunt ut labore et dolore magna aliqua. Lorem ipsum dolor sit amet, consectetur adipiscing elit.</div>
    <div style="display:flex;align-items:center;gap:6px;margin-top:12px"><span style="width:18px;height:18px;border-radius:50%;background:#d6d6d6;display:inline-block" role="img" aria-label="Avatar placeholder"></span><span style="font-size:5.5px;color:var(--navy);font-weight:600">Your Name<br><span style="font-weight:400;color:var(--muted)">Founder</span></span></div>
  </div>
</section>

<!-- 33 statistics circles -->
<section class="slide">
  <div class="corner"></div><div class="side">Ledger Lanternfox</div><div class="pg">33</div>
  <div class="hd center" style="top:22px;font-size:15px">Here Is Statistics</div>
  <svg class="abs" style="left:30px;top:55px" width="160" height="150" aria-hidden="true">
    <circle cx="58" cy="75" r="58" fill="#1c3f7f"/>
    <circle cx="58" cy="96" r="37" fill="#e8262c"/>
    <circle cx="58" cy="114" r="19" fill="#7b7b7b"/>
    <text x="58" y="36" fill="#fff" font-size="13" font-weight="600" text-anchor="middle" font-family="Poppins, sans-serif">$</text>
    <text x="58" y="85" fill="#fff" font-size="13" font-weight="600" text-anchor="middle" font-family="Poppins, sans-serif">$</text>
    <text x="58" y="119" fill="#fff" font-size="10" font-weight="600" text-anchor="middle" font-family="Poppins, sans-serif">$</text>
    <line x1="58" y1="30" x2="128" y2="30" stroke="#1c3f7f" stroke-width=".6"/>
    <line x1="58" y1="68" x2="128" y2="68" stroke="#e8262c" stroke-width=".6"/>
    <line x1="58" y1="108" x2="128" y2="108" stroke="#7b7b7b" stroke-width=".6"/>
    <text x="132" y="33" font-size="10" font-weight="600" fill="#1c3f7f" font-family="Poppins, sans-serif">5M</text>
    <text x="132" y="71" font-size="10" font-weight="600" fill="#1c3f7f" font-family="Poppins, sans-serif">2M</text>
    <text x="132" y="111" font-size="10" font-weight="600" fill="#1c3f7f" font-family="Poppins, sans-serif">1M</text>
  </svg>
  <div class="abs" style="left:225px;top:70px;width:150px;display:flex;flex-direction:column;gap:14px">
    <div style="display:flex;gap:8px"><svg width="12" height="12" aria-hidden="true"><rect width="12" height="12" fill="#1c3f7f"/><path d="M3 6 L5 8.5 L9.5 3.5" stroke="#fff" stroke-width="1.3" fill="none"/></svg><div class="tiny"><b style="color:var(--navy);font-size:5.5px">Lorem ipsum dolor</b><br>Lorem ipsum dolor sit amet, consectetur adipiscing elit, sed do eiusmod tempor</div></div>
    <div style="display:flex;gap:8px"><svg width="12" height="12" aria-hidden="true"><rect width="12" height="12" fill="#e8262c"/><path d="M3 6 L5 8.5 L9.5 3.5" stroke="#fff" stroke-width="1.3" fill="none"/></svg><div class="tiny"><b style="color:var(--navy);font-size:5.5px">Lorem ipsum dolor</b><br>Lorem ipsum dolor sit amet, consectetur adipiscing elit, sed do eiusmod tempor</div></div>
    <div style="display:flex;gap:8px"><svg width="12" height="12" aria-hidden="true"><rect width="12" height="12" fill="#7b7b7b"/><path d="M3 6 L5 8.5 L9.5 3.5" stroke="#fff" stroke-width="1.3" fill="none"/></svg><div class="tiny"><b style="color:var(--navy);font-size:5.5px">Lorem ipsum dolor</b><br>Lorem ipsum dolor sit amet, consectetur adipiscing elit, sed do eiusmod tempor</div></div>
  </div>
</section>

<!-- 34 percentages -->
<section class="slide">
  <div class="corner"></div><div class="side">Ledger Lanternfox</div><div class="pg">34</div>
  <div class="hd center" style="top:20px;font-size:15px">Here Add Your Title</div>
  <div class="abs tiny" style="left:70px;right:50px;top:62px;text-align:center">Lorem Ipsum the printing and typesetting industry. Lorem Ipsum has been the industry's standard dummy text ever since the 1500s, when an unknown printer took a galley of type and scrambled it to make a type specimen book. It has survived not only five centuries.</div>
  <svg class="abs" style="left:76px;top:100px" width="250" height="56" aria-hidden="true" font-family="Poppins, sans-serif">
    <circle cx="28" cy="28" r="24" fill="none" stroke="#eee" stroke-width="3"/><circle cx="28" cy="28" r="24" fill="none" stroke="#e8262c" stroke-width="3" stroke-dasharray="75.4 150.8" transform="rotate(-90 28 28)"/><text x="28" y="32" text-anchor="middle" font-size="11" font-weight="600" fill="#1c3f7f">50%</text>
    <circle cx="110" cy="28" r="24" fill="none" stroke="#eee" stroke-width="3"/><circle cx="110" cy="28" r="24" fill="none" stroke="#e8262c" stroke-width="3" stroke-dasharray="113 150.8" transform="rotate(-90 110 28)"/><text x="110" y="32" text-anchor="middle" font-size="11" font-weight="600" fill="#1c3f7f">75%</text>
    <circle cx="192" cy="28" r="24" fill="none" stroke="#eee" stroke-width="3"/><circle cx="192" cy="28" r="24" fill="none" stroke="#e8262c" stroke-width="3" stroke-dasharray="60.3 150.8" transform="rotate(-90 192 28)"/><text x="192" y="32" text-anchor="middle" font-size="11" font-weight="600" fill="#1c3f7f">40%</text>
  </svg>
  <div class="abs tiny" style="left:76px;top:164px;width:60px;text-align:center">Lorem ipsum dolor amet consectetur dolor</div>
  <div class="abs tiny" style="left:158px;top:164px;width:60px;text-align:center">Lorem ipsum dolor amet consectetur dolor</div>
  <div class="abs tiny" style="left:240px;top:164px;width:60px;text-align:center">Lorem ipsum dolor amet consectetur dolor</div>
</section>

<!-- 35 line chart -->
<section class="slide">
  <div class="corner"></div><div class="side">Ledger Lanternfox</div><div class="pg">35</div>
  <div class="hd center" style="top:18px;font-size:15px">Here is Statistics</div>
  <div class="abs" style="left:28px;top:66px;width:96px;height:126px;box-shadow:0 2px 8px rgba(0,0,0,.12);background:#fff">
    <div class="bg-navy" style="height:56px;color:#fff;text-align:center;padding-top:12px;font-size:15px;font-weight:500">$0.5M<div style="font-size:4.5px;opacity:.8">Revenue</div></div>
    <div style="text-align:center;padding-top:14px;font-size:13px;color:var(--red)">-0.28%<div style="font-size:4.5px;color:var(--red-soft)">Revenue</div></div>
  </div>
  <svg class="abs" style="left:140px;top:60px" width="236" height="140" aria-hidden="true" font-family="Poppins, sans-serif" font-size="4">
    <g fill="#888" text-anchor="end">
      <text x="16" y="10">$350,000</text><text x="16" y="26">$300,000</text><text x="16" y="42">$250,000</text><text x="16" y="58">$200,000</text><text x="16" y="74">$150,000</text><text x="16" y="90">$100,000</text><text x="16" y="106">$50,000</text><text x="16" y="122">$</text>
    </g>
    <polyline fill="none" stroke="#e8262c" stroke-width="1" points="22,120 38,116 54,94 70,102 86,90 102,98 118,84 134,96 150,72 166,90 182,62 198,84 214,50 230,30"/>
    <g fill="#888" text-anchor="middle">
      <text x="22" y="132">Jan</text><text x="40" y="132">Feb</text><text x="58" y="132">Mar</text><text x="76" y="132">Apr</text><text x="94" y="132">May</text><text x="112" y="132">Jun</text><text x="130" y="132">Jul</text><text x="148" y="132">Aug</text><text x="166" y="132">Sep</text><text x="184" y="132">Oct</text><text x="202" y="132">Nov</text><text x="220" y="132">Dec</text>
    </g>
  </svg>
</section>

<!-- 36 timeline -->
<section class="slide">
  <div class="corner"></div><div class="side">Ledger Lanternfox</div><div class="pg">36</div>
  <div class="hd center" style="top:22px;font-size:15px">Company Timeline</div>
  <svg class="abs" style="left:30px;top:80px" width="340" height="30" aria-hidden="true" font-family="Poppins, sans-serif" font-size="7" font-weight="600" fill="#fff">
    <polygon points="0,0 58,0 68,15 58,30 0,30 10,15" fill="#e8262c"/>
    <polygon points="64,0 122,0 132,15 122,30 64,30 74,15" fill="#1c3f7f"/>
    <polygon points="128,0 186,0 196,15 186,30 128,30 138,15" fill="#e8262c"/>
    <polygon points="192,0 250,0 260,15 250,30 192,30 202,15" fill="#1c3f7f"/>
    <polygon points="256,0 314,0 324,15 314,30 256,30 266,15" fill="#e8262c"/>
    <text x="36" y="18" text-anchor="middle">STEP 01</text><text x="100" y="18" text-anchor="middle">STEP 02</text><text x="164" y="18" text-anchor="middle">STEP 03</text><text x="228" y="18" text-anchor="middle">STEP 04</text><text x="292" y="18" text-anchor="middle">STEP 05</text>
  </svg>
  <div class="abs" style="left:34px;top:132px;width:330px;display:flex;justify-content:space-between">
    <div style="width:58px;text-align:center"><div style="font-size:5.5px;font-weight:600;margin-bottom:2px">Project name</div><div class="tiny">Lorem Ipsum is simply dummy unknown printer took a galley of type to make</div></div>
    <div style="width:58px;text-align:center"><div style="font-size:5.5px;font-weight:600;margin-bottom:2px">Project name</div><div class="tiny">Lorem Ipsum is simply dummy unknown printer took a galley of type to make</div></div>
    <div style="width:58px;text-align:center"><div style="font-size:5.5px;font-weight:600;margin-bottom:2px">Project name</div><div class="tiny">Lorem Ipsum is simply dummy unknown printer took a galley of type to make</div></div>
    <div style="width:58px;text-align:center"><div style="font-size:5.5px;font-weight:600;margin-bottom:2px">Project name</div><div class="tiny">Lorem Ipsum is simply dummy unknown printer took a galley of type to make</div></div>
    <div style="width:58px;text-align:center"><div style="font-size:5.5px;font-weight:600;margin-bottom:2px">Project name</div><div class="tiny">Lorem Ipsum is simply dummy unknown printer took a galley of type to make</div></div>
  </div>
</section>

<!-- 37 Q&A -->
<section class="slide">
  <div class="corner"></div><div class="side">Ledger Lanternfox</div><div class="pg">37</div>
  <div class="hd center" style="top:18px;font-size:15px">Q&amp;A Slide</div>
  <div class="abs" style="left:50px;top:58px;width:310px;display:grid;grid-template-columns:1fr 1fr;column-gap:24px;row-gap:12px">
    <div style="display:flex;gap:8px"><span class="bg-navy" style="flex:0 0 20px;height:20px;border-radius:3px;color:#fff;font-size:10px;font-weight:600;text-align:center;line-height:20px">Q</span><span class="tiny">Lorem Ipsum is simply dummy unknown printer took a galley of type and scrambled it to make</span></div>
    <div style="display:flex;gap:8px"><span class="bg-red" style="flex:0 0 20px;height:20px;border-radius:3px;color:#fff;font-size:10px;font-weight:600;text-align:center;line-height:20px">A</span><span class="tiny">type and scrambled it to make Lorem Ipsum is simply dummy unknown printer took a galley of</span></div>
    <div style="display:flex;gap:8px"><span class="bg-navy" style="flex:0 0 20px;height:20px;border-radius:3px;color:#fff;font-size:10px;font-weight:600;text-align:center;line-height:20px">Q</span><span class="tiny">Lorem Ipsum is simply dummy unknown printer took a galley of type and scrambled it to make</span></div>
    <div style="display:flex;gap:8px"><span class="bg-red" style="flex:0 0 20px;height:20px;border-radius:3px;color:#fff;font-size:10px;font-weight:600;text-align:center;line-height:20px">A</span><span class="tiny">Lorem Ipsum is simply dummy unknown printer took a galley of type and scrambled it to make</span></div>
    <div style="display:flex;gap:8px"><span class="bg-navy" style="flex:0 0 20px;height:20px;border-radius:3px;color:#fff;font-size:10px;font-weight:600;text-align:center;line-height:20px">Q</span><span class="tiny">Lorem Ipsum is simply dummy unknown printer took a galley of type and scrambled it to make</span></div>
    <div style="display:flex;gap:8px"><span class="bg-red" style="flex:0 0 20px;height:20px;border-radius:3px;color:#fff;font-size:10px;font-weight:600;text-align:center;line-height:20px">A</span><span class="tiny">Lorem Ipsum is simply dummy unknown printer took a galley of type and scrambled it to make</span></div>
    <div style="display:flex;gap:8px"><span class="bg-navy" style="flex:0 0 20px;height:20px;border-radius:3px;color:#fff;font-size:10px;font-weight:600;text-align:center;line-height:20px">Q</span><span class="tiny">Lorem Ipsum is simply dummy unknown printer took a galley of type and scrambled it to make</span></div>
    <div style="display:flex;gap:8px"><span class="bg-red" style="flex:0 0 20px;height:20px;border-radius:3px;color:#fff;font-size:10px;font-weight:600;text-align:center;line-height:20px">A</span><span class="tiny">Lorem Ipsum is simply dummy unknown printer took a galley of type and scrambled it to make</span></div>
  </div>
</section>

<!-- 38 thank you -->
<section class="slide">
  <div class="photo" style="inset:0;background:linear-gradient(135deg,#f4f5f8,#e9ecf1)" role="img" aria-label="Faint light photo of a building structure"></div>
  <div class="abs" style="left:54px;top:50px"><span class="brand" style="font-size:9px"><span class="dot"></span>Ledger Lanternfox</span></div>
  <div class="abs" style="left:42px;top:84px;width:106px;background:#fff;box-shadow:0 2px 8px rgba(0,0,0,.12)">
    <div class="bg-navy tiny white-t" style="padding:7px 8px;display:flex;gap:8px;align-items:center">● <span>www.website.com</span></div>
    <div class="tiny" style="padding:7px 8px;display:flex;gap:8px;align-items:center;color:var(--navy)">● <span style="color:var(--muted)">Here to write your<br>Company adress</span></div>
    <div class="tiny" style="padding:7px 8px;display:flex;gap:8px;align-items:center;color:var(--navy);border-top:1px solid var(--line)">● <span style="color:var(--muted)">info@website.com</span></div>
  </div>
  <div class="abs" style="left:200px;top:92px;color:var(--navy);font-weight:600;font-size:22px">THANK YOU</div>
</section>

<!-- 39 questions -->
<section class="slide">
  <div class="corner"></div><div class="side">Ledger Lanternfox</div><div class="pg">39</div>
  <svg class="abs" style="left:88px;top:20px" width="232" height="180" aria-hidden="true">
    <polygon points="6,28 218,6 226,132 134,142 114,172 102,146 14,150" fill="none" stroke="#1c3f7f" stroke-width="1.2"/>
    <polygon points="2,36 212,16 222,126 128,134 110,162 98,140 8,142" fill="none" stroke="#e8262c" stroke-width="1.2"/>
    <polygon points="14,40 206,22 214,120 124,128 108,152 96,134 18,136" fill="#fff" stroke="#1c3f7f" stroke-width=".6"/>
  </svg>
  <div class="abs" style="left:0;right:0;top:92px;text-align:center;color:var(--navy);font-weight:600;font-size:21px;padding-left:20px">Questions?</div>
</section>

</main>
</body>
</html>
```